Business Card for Coastal Tundrabridge Advisory

We need a business card for Coastal Tundrabridge Advisory. The company website address is provided below. The company logo is attached. We provide specialized permafrost services to the mining, transportation, and oil & gas industries. The card should be prepared for:
Matthias Korhonen, PhD.
Coastal Tundrabridge Advisory
PO Box 418259
Quillwater, Alaska 99642
Direct: +1-907-555-0143
Email: mkorhonen@tundrabridgeadvisory.example
Website: www.coastaltundrabridgeadvisory.example

```html
<!DOCTYPE html>
<html lang="en">
<head>
<meta charset="utf-8">
<title>Coastal Tundrabridge Advisory — Business Card</title>
<link href="https://fonts.googleapis.com/css2?family=Montserrat:wght@400;500;700&display=swap" rel="stylesheet">
<style>
  :root {
    --backdrop: #3b3b3c;
    --ink: #121a24;
    --paper: #ffffff;
    --muted: #2a2f36;
  }
  * { box-sizing: border-box; margin: 0; padding: 0; }
  html, body {
    width: 1200px; height: 1200px; overflow: hidden;
    background: var(--backdrop);
    font-family: "Montserrat", sans-serif;
  }
  .stage {
    width: 1200px; height: 1200px;
    display: flex; flex-direction: column; align-items: center; justify-content: center;
    gap: 60px;
  }
  .card {
    width: 860px; height: 491px;
    position: relative;
  }
  .card--back {
    background: var(--ink);
    display: flex; align-items: center; justify-content: center;
  }
  .wordmark {
    font-weight: 500;
    text-transform: uppercase;
    letter-spacing: 0.14em;
    line-height: 1.25;
  }
  .card--back .wordmark {
    color: var(--paper);
    font-size: 34px;
    text-align: center;
  }
  .card--front {
    background: var(--paper);
    color: var(--ink);
  }
  .card--front .wordmark {
    position: absolute; right: 60px; top: 118px;
    font-size: 24px; text-align: right;
    color: var(--ink);
  }
  .person { position: absolute; left: 60px; top: 62px; }
  .person__name { font-weight: 700; font-size: 27px; letter-spacing: 0.005em; }
  .person__role { font-size: 17px; margin-top: 4px; color: var(--muted); }
  .contact {
    position: absolute; left: 300px; bottom: 52px;
    font-size: 18px; line-height: 1.3; color: var(--muted);
  }
  .contact__address { margin-bottom: 22px; }
  .contact__list { list-style: none; }
  .contact__item { display: flex; align-items: center; gap: 14px; margin-top: 6px; }
  .contact__icon { width: 18px; height: 18px; flex: none; }
</style>
</head>
<body>
<main class="stage">
  <section class="card card--back" aria-label="Card back">
    <div class="wordmark">Coastal Tundrabridge<br>Advisory</div>
  </section>

  <section class="card card--front" aria-label="Card front">
    <div class="person">
      <div class="person__name">Matthias Korhonen, PhD.</div>
      <div class="person__role">Managing Director</div>
    </div>

    <div class="wordmark">Coastal Tundrabridge<br>Advisory</div>

    <div class="contact">
      <div class="contact__address">PO Box 418259<br>Quillwater, Alaska 99642</div>
      <ul class="contact__list">
        <li class="contact__item">
          <svg class="contact__icon" viewBox="0 0 24 24"><circle cx="12" cy="12" r="12" fill="#121a24"/><path d="M8 6.5l2 .3 1 3-1.4 1a7 7 0 0 0 3.6 3.6l1-1.4 3 1 .3 2c-.5 1-1.5 1.5-2.5 1.4A10 10 0 0 1 6.6 9c-.1-1 .4-2 1.4-2.5z" fill="#fff"/></svg>
          <span>+1-907-555-0143</span>
        </li>
        <li class="contact__item">
          <svg class="contact__icon" viewBox="0 0 24 24"><rect x="2" y="5" width="20" height="14" rx="1.5" fill="#121a24"/><path d="M3 6l9 7 9-7" fill="none" stroke="#fff" stroke-width="1.6"/></svg>
          <span>mkorhonen@tundrabridgeadvisory.example</span>
        </li>
        <li class="contact__item">
          <svg class="contact__icon" viewBox="0 0 24 24"><circle cx="12" cy="12" r="11" fill="#121a24"/><g fill="none" stroke="#fff" stroke-width="1.3"><ellipse cx="12" cy="12" rx="4.5" ry="10"/><path d="M2 12h20M4 7h16M4 17h16"/></g></svg>
          <span>www.coastaltundrabridgeadvisory.example</span>
        </li>
      </ul>
    </div>
  </section>
</main>
</body>
</html>
```